Business card design for Automotive workshop

We need a business card for a new automotive repair and tyre shop called Keelstone Prime Automotive located in New Zealand. We are a clean, modern and fresh workshop and company.

Front needs to feature logo,
my name:
Marlo Fenwicke (director)

Address:
48 Tarn Lane
Whitianga 3510

Phone: 07 594 2713
Mobile: 027 451 9362
Email: office@keelstoneautomotive.example.nz
Website: keelstoneautomotive.example.nz

Back needs to feature an area to write down appointment details, date and time.

Also feature a list of jobs and work we do such as,
Vehicle Servicing
All Mechanical Repairs
Warrant of Fitness
Tyres & Wheel Alignments
Automotive Diagnostics
Automotive Parts & Supplies

```html
<!DOCTYPE html>
<html lang="en">
<head>
<meta charset="utf-8">
<title>Keelstone Prime Automotive – Business Card</title>
<link href="https://fonts.googleapis.com/css2?family=Exo+2:ital,wght@0,400;0,500;0,700;0,800;1,400&display=swap" rel="stylesheet">
<style>
  :root {
    --ink: #0b0b0c;
    --red: #e01e25;
    --white: #ffffff;
    --grey: #3a3a3c;
    --backdrop: #2a2c30;
  }
  * { box-sizing: border-box; margin: 0; padding: 0; }
  html, body {
    width: 1200px; height: 900px; overflow: hidden;
    background: var(--backdrop);
    font-family: "Exo 2", Arial, sans-serif;
  }
  .canvas { position: relative; width: 1200px; height: 900px; }
  .card {
    position: absolute; left: 250px; width: 700px; height: 400px;
    overflow: hidden; box-shadow: 0 10px 30px rgba(0,0,0,.45);
  }
  .card-front { top: 40px; background: var(--ink); color: var(--white); }
  .card-back { top: 460px; background: var(--white); color: var(--ink); }
  .card-shapes { position: absolute; inset: 0; width: 700px; height: 400px; }

  .brand { position: absolute; }
  .brand-name {
    font-weight: 800; font-size: 30px; letter-spacing: 1px;
    text-transform: uppercase; line-height: 1; color: var(--white);
    display: flex; align-items: center; gap: 10px; white-space: nowrap;
  }
  .brand-mark { width: 14px; height: 14px; background: var(--red); flex: none; }
  .card-front .brand { left: 40px; top: 38px; }
  .card-back .brand { right: 36px; top: 46px; }
  .card-back .brand-name { font-size: 26px; }
  .card-back .brand-mark { width: 12px; height: 12px; }

  .person { position: absolute; left: 40px; top: 118px; }
  .person-name {
    color: var(--red); font-weight: 800; font-size: 30px;
    letter-spacing: 2px; text-transform: uppercase;
  }
  .person-role { font-size: 18px; margin-top: 2px; }
  .divider {
    position: absolute; left: 40px; right: 40px; top: 200px;
    height: 1px; background: var(--white);
  }
  .contacts { position: absolute; left: 40px; top: 216px; list-style: none; }
  .contacts li {
    display: flex; align-items: center; gap: 10px;
    font-size: 17px; line-height: 24px;
  }
  .contacts svg { width: 14px; height: 14px; flex: none; }
  .address {
    position: absolute; left: 40px; top: 346px;
    font-size: 18px; font-weight: 500; color: var(--ink);
  }

  .services { position: absolute; list-style: none; font-size: 15px; text-transform: uppercase; letter-spacing: .5px; line-height: 22px; }
  .services li { display: flex; align-items: center; gap: 8px; }
  .services li::before, .services-right li::after {
    content: ""; width: 8px; height: 8px; border-radius: 50%; background: var(--red); flex: none;
  }
  .services-left { left: 40px; top: 138px; }
  .services-right { right: 36px; top: 142px; text-align: right; }
  .services-right li { justify-content: flex-end; }
  .services-right li::before { display: none; }

  .write-line {
    position: absolute; right: 36px; height: 0;
    border-top: 1.5px dashed #555;
  }
  .line-blank { left: 40px; top: 240px; }
  .line-date { left: 100px; top: 290px; }
  .line-time { left: 290px; top: 345px; }
  .field-label {
    position: absolute; color: var(--red); font-size: 15px;
    font-weight: 500; text-transform: uppercase;
  }
  .label-date { left: 40px; top: 276px; }
  .label-time { left: 232px; top: 333px; }
</style>
</head>
<body>
<main class="canvas">

  <section class="card card-front" aria-label="Business card front">
    <svg class="card-shapes" viewBox="0 0 700 400" aria-hidden="true">
      <polygon points="0,330 430,330 400,400 0,400" fill="var(--white)"/>
      <polygon points="440,330 520,330 490,400 410,400" fill="var(--red)"/>
    </svg>
    <div class="brand">
      <div class="brand-name"><span class="brand-mark"></span>Keelstone Prime Automotive</div>
    </div>
    <div class="person">
      <h1 class="person-name">Marlo Fenwicke</h1>
      <p class="person-role">Director</p>
    </div>
    <div class="divider"></div>
    <ul class="contacts">
      <li><svg viewBox="0 0 14 14"><path d="M3 1h3l1 3-2 1a7 7 0 0 0 4 4l1-2 3 1v3a1 1 0 0 1-1 1A12 12 0 0 1 2 2a1 1 0 0 1 1-1z" fill="none" stroke="var(--red)" stroke-width="1.3"/></svg>07 594 2713</li>
      <li><svg viewBox="0 0 14 14"><rect x="3.5" y="1" width="7" height="12" rx="1.2" fill="none" stroke="var(--red)" stroke-width="1.3"/><circle cx="7" cy="11" r=".8" fill="var(--red)"/></svg>027 451 9362</li>
      <li><svg viewBox="0 0 14 14"><rect x="1" y="3" width="12" height="8" fill="none" stroke="var(--red)" stroke-width="1.3"/><path d="M1 3l6 5 6-5" fill="none" stroke="var(--red)" stroke-width="1.3"/></svg>office@keelstoneautomotive.example.nz</li>
      <li><svg viewBox="0 0 14 14"><circle cx="7" cy="7" r="6" fill="none" stroke="var(--red)" stroke-width="1.3"/><path d="M1 7h12M7 1c-3 3.5-3 8.5 0 12M7 1c3 3.5 3 8.5 0 12" fill="none" stroke="var(--red)" stroke-width="1.1"/></svg>keelstoneautomotive.example.nz</li>
    </ul>
    <p class="address">48 Tarn Lane, Whitianga 3510</p>
  </section>

  <section class="card card-back" aria-label="Business card back, appointment card">
    <svg class="card-shapes" viewBox="0 0 700 400" aria-hidden="true">
      <polygon points="0,0 96,0 0,48" fill="var(--red)"/>
      <polygon points="120,0 700,0 700,120 240,120" fill="var(--ink)"/>
      <polygon points="0,310 200,310 170,400 0,400" fill="var(--ink)"/>
      <polygon points="0,302 52,302 48,310 0,310" fill="var(--red)"/>
    </svg>
    <div class="brand">
      <div class="brand-name"><span class="brand-mark"></span>Keelstone Prime Automotive</div>
    </div>
    <ul class="services services-left">
      <li>Vehicle Servicing</li>
      <li>All Mechanical Repairs</li>
      <li>Warrant of Fitness</li>
    </ul>
    <ul class="services services-right">
      <li>Tyres &amp; Wheel Alignments</li>
      <li>Automotive Diagnostics</li>
      <li>Automotive Parts &amp; Supplies</li>
    </ul>
    <div class="write-line line-blank"></div>
    <span class="field-label label-date">Date:</span>
    <div class="write-line line-date"></div>
    <span class="field-label label-time">Time:</span>
    <div class="write-line line-time"></div>
  </section>

</main>
</body>
</html>
```